Business Cards Design for the electrical wholesaler: clean bold dynamic :)

We need a business card design that would follow our latest brand guidelines. As an electrical wholesaler we want to bring a fresh look and feel into the industry. The design should be clean bold and dynamic. It should come alive with the renewed energy of our green colour. Our grey colour should keep things balanced and complement the notion of maturity and responsibility. We employ Lato as a corporate font however are not bound by this font and we’re open to interpretation here.

Target Market(s)

Electrical contractors

Industry/Entity Type

Business

Contact Information for Business Card

Logo
Name & Surname: Halyna Dorosh
Job Title: Director of Marketing
Email: halya.dorosh@quillmail.example
Cell phone: 780.555.0147
Address: 20517 - 87 Ave. Edmonton, AB, Canada. T6K 4N8
Business Phone: 780.555.0184
Website: www.brovix.example

Font styles to use
Other font styles liked:
• Lato

Requirements
Must have
• Logo & website
Nice to have
• Brand elements - some of them you may find in the attached Brand Guidelines (e.g. three lines on the background signifying "W")

```html
<!DOCTYPE html>
<html lang="en">
<head>
<meta charset="utf-8">
<title>Brovix Business Card</title>
<link rel="stylesheet" href="https://fonts.googleapis.com/css2?family=Oswald:wght@500&family=Work+Sans:wght@400;500&display=swap">
<style>
  :root {
    --backdrop: #161616;
    --card: #262626;
    --card-edge: #2f2f2f;
    --green: #7ccb3a;
    --grey-light: #c9c9c9;
    --white: #f2f2f2;
  }
  * { box-sizing: border-box; margin: 0; padding: 0; }
  html, body { width: 1200px; height: 900px; overflow: hidden; }
  body {
    background: var(--backdrop);
    font-family: "Work Sans", Arial, sans-serif;
    position: relative;
  }
  .card {
    position: absolute;
    left: 270px;
    width: 660px;
    height: 377px;
    background: linear-gradient(135deg, var(--card) 0%, #2c2c2c 60%, var(--card-edge) 100%);
    border-bottom: 5px solid var(--green);
    box-shadow: 0 18px 40px rgba(0,0,0,0.55);
    overflow: hidden;
  }
  .card--front { top: 40px; }
  .card--back { top: 470px; }

  .brand-name {
    position: absolute;
    left: 0; right: 0;
    top: 140px;
    text-align: center;
    font-family: "Work Sans", Arial, sans-serif;
    font-weight: 500;
    font-size: 78px;
    letter-spacing: 1px;
    color: var(--grey-light);
  }

  .identity {
    position: absolute;
    right: 385px;
    top: 120px;
    text-align: right;
    white-space: nowrap;
  }
  .identity__name {
    font-family: "Oswald", "Arial Narrow", sans-serif;
    font-weight: 500;
    font-size: 36px;
    line-height: 1.05;
    color: var(--green);
    text-transform: uppercase;
    letter-spacing: 0.5px;
  }
  .identity__title {
    font-size: 16px;
    color: var(--white);
    margin-top: 6px;
    letter-spacing: 1px;
  }
  .divider {
    position: absolute;
    left: 292px;
    top: 112px;
    width: 2px;
    height: 104px;
    background: var(--green);
  }
  .contacts {
    position: absolute;
    left: 312px;
    top: 112px;
    list-style: none;
  }
  .contacts li {
    display: flex;
    align-items: center;
    gap: 10px;
    font-size: 16px;
    letter-spacing: 0.5px;
    color: var(--white);
    height: 26px;
    white-space: nowrap;
  }
  .contacts svg { width: 14px; height: 14px; flex: none; }
  .accent { color: var(--green); }
  .address {
    position: absolute;
    left: 70px;
    bottom: 50px;
    font-size: 19px;
    letter-spacing: 1.5px;
    color: var(--white);
  }
</style>
</head>
<body>
  <section class="card card--front">
    <div class="brand-name">brovix</div>
  </section>

  <section class="card card--back">
    <div class="identity">
      <div class="identity__name">Halyna Dorosh</div>
      <div class="identity__title">Director of Marketing</div>
    </div>
    <div class="divider"></div>
    <ul class="contacts">
      <li>
        <svg viewBox="0 0 14 14" aria-hidden="true"><path d="M3 1.5 L5 1.5 L6 4.5 L4.6 5.6 Q6 8.6 8.4 9.4 L9.5 8 L12.5 9 L12.5 11 Q12.5 12.5 11 12.5 Q2 12 1.5 3 Q1.5 1.5 3 1.5 Z" fill="none" stroke="var(--green)" stroke-width="1.3"/></svg>
        780.555.0184
      </li>
      <li>
        <svg viewBox="0 0 14 14" aria-hidden="true"><rect x="3.5" y="1" width="7" height="12" rx="1.5" fill="none" stroke="var(--green)" stroke-width="1.3"/><path d="M6 11 H8" stroke="var(--green)" stroke-width="1.3"/></svg>
        780.555.0147
      </li>
      <li>
        <svg viewBox="0 0 14 14" aria-hidden="true"><rect x="1.5" y="3" width="11" height="8" fill="none" stroke="var(--green)" stroke-width="1.3"/><path d="M1.5 3 L7 7.5 L12.5 3" fill="none" stroke="var(--green)" stroke-width="1.3"/></svg>
        halya.dorosh@quillmail.example
      </li>
      <li>
        <svg viewBox="0 0 14 14" aria-hidden="true"><circle cx="7" cy="7" r="5.5" fill="none" stroke="var(--green)" stroke-width="1.2"/><ellipse cx="7" cy="7" rx="2.4" ry="5.5" fill="none" stroke="var(--green)" stroke-width="1.1"/><path d="M1.5 7 H12.5 M2.5 4.2 H11.5 M2.5 9.8 H11.5" stroke="var(--green)" stroke-width="1.1"/></svg>
        <span>www.<span class="accent">brovix</span>.example</span>
      </li>
    </ul>
    <div class="address">20517 87ave T6K4N8 Edmonton, Alberta</div>
  </section>
</body>
</html>
```